Business Card Design Project

We need a business card for a new technology services company. We develop software and implement software packages for our business customers and although we will begin with just one or two service offerings, our service offerings will expand over time. Our name comes from the an author, KL Barrow, and his "idea" was that opportunity should be based on ability and achievement, not on social status.

We would like to see a design that is standard in its size and shape, but stands apart in its dramatic color contrasts. The card should not use too many colors - the colors used in the background should highlight the brilliant blues of the logo (see attachment) to dramatic effect. The background should not be white.

If necessary, you can change the color of the words "KL Barrow", but not the word "Idea".

Card size should be U.S. standard 2 inches by 3.5 inches and provide for 1/8 inch bleed area on each side.

We need a design for both sides of the business card, one side communicating the company logo and contact information, the other side being purely graphical, incorporating the logo but no other information.

Contact Information Required:
Kate Brook
KateBrook@klbarrowvista.com
614-387-2259

Target Market(s)

Business executives

Industry/Entity Type

Software

Requirements
Must have
• It must have the full company logo on one side, and at least the graphic element of the logo on the other. Either that or the full logo on both.
Nice to have
• It would be nice to have a design that could work without needing two different textures. For example, it would be nice if the entire card could be shiny, not just parts of the card.

It would also be nice if texture is something we could add later.
Should not have
• The card should not use the color green.

```html
<!DOCTYPE html>
<html lang="en">
<head>
<meta charset="utf-8">
<title>Cobalt Vista – Business Card</title>
<link rel="stylesheet" href="https://fonts.googleapis.com/css2?family=Arimo:wght@400&family=Cinzel:wght@400&family=Inter:wght@300&display=swap">
<style>
  :root {
    --page: #e9e7e4;
    --card-dark: #1e1f21;
    --card-mid: #35373a;
    --brand-blue: #1ea5e0;
    --brand-blue-soft: rgba(30, 165, 224, 0.16);
    --rule-grey: #8c8f93;
    --text-light: #f2f2f2;
  }
  * { box-sizing: border-box; margin: 0; padding: 0; }
  html, body { width: 1200px; height: 750px; overflow: hidden; }
  body {
    background: var(--page);
    position: relative;
    font-family: "Arimo", Arial, sans-serif;
  }
  .card {
    position: absolute;
    top: 226px;
    width: 525px;
    height: 300px;
    border-radius: 20px;
    overflow: hidden;
    background: radial-gradient(ellipse at 55% 40%, var(--card-mid) 0%, var(--card-dark) 75%);
    box-shadow: 0 8px 24px rgba(0, 0, 0, 0.25);
  }
  .card--front { left: 50px; }
  .card--back {
    left: 625px;
    background:
      radial-gradient(circle at 48% 50%, var(--brand-blue-soft) 0%, rgba(30, 165, 224, 0) 45%),
      radial-gradient(ellipse at 55% 40%, var(--card-mid) 0%, var(--card-dark) 75%);
  }

  .wordmark {
    position: absolute;
    font-family: "Inter", Arial, sans-serif;
    font-weight: 300;
    color: var(--brand-blue);
    letter-spacing: -0.5px;
    white-space: nowrap;
    display: flex;
    align-items: center;
    line-height: 1;
  }
  .card--front .wordmark { left: 38px; top: 96px; font-size: 36px; }
  .wordmark__dot {
    display: inline-block;
    width: 12px; height: 12px;
    border-radius: 50%;
    background: var(--brand-blue);
    margin-left: 10px;
  }

  .holder-name {
    position: absolute;
    left: 38px; top: 156px;
    font-family: "Cinzel", Georgia, serif;
    font-weight: 400;
    font-size: 20px;
    color: var(--brand-blue);
    letter-spacing: 1px;
    text-transform: uppercase;
  }
  .contact {
    position: absolute;
    left: 38px; top: 196px;
    list-style: none;
    color: var(--text-light);
    font-size: 13px;
  }
  .contact__item { display: flex; align-items: center; gap: 8px; margin-bottom: 7px; }
  .contact__icon { width: 11px; height: 11px; fill: var(--brand-blue); flex: none; }

  .stripe-rule {
    position: absolute; left: 0; right: 0; bottom: 44px;
    height: 3px; background: var(--rule-grey);
  }
  .stripe-band {
    position: absolute; left: 0; right: 0; bottom: 0;
    height: 38px; background: var(--brand-blue);
  }

  .card--back .wordmark {
    left: 50%; top: 50%;
    transform: translate(-50%, -50%);
    font-size: 62px;
  }
</style>
</head>
<body>
  <section class="card card--front" aria-label="Business card front">
    <div class="wordmark">Cobalt Vista<span class="wordmark__dot"></span></div>
    <h1 class="holder-name">Kate Brook</h1>
    <ul class="contact">
      <li class="contact__item">
        <svg class="contact__icon" viewBox="0 0 24 24" aria-hidden="true"><path d="M6.6 10.8a15.1 15.1 0 0 0 6.6 6.6l2.2-2.2a1 1 0 0 1 1-.25 11.4 11.4 0 0 0 3.6.57 1 1 0 0 1 1 1V20a1 1 0 0 1-1 1A17 17 0 0 1 3 4a1 1 0 0 1 1-1h3.5a1 1 0 0 1 1 1c0 1.25.2 2.45.57 3.57a1 1 0 0 1-.25 1z"/></svg>
        <span>614-387-2259</span>
      </li>
      <li class="contact__item">
        <svg class="contact__icon" viewBox="0 0 24 24" aria-hidden="true"><path d="M2 5h20v14H2z M4 7v.5l8 5 8-5V7l-8 5z" fill-rule="evenodd"/></svg>
        <span>KateBrook@klbarrowvista.com</span>
      </li>
    </ul>
    <div class="stripe-rule"></div>
    <div class="stripe-band"></div>
  </section>

  <section class="card card--back" aria-label="Business card back">
    <div class="wordmark">Cobalt Vista</div>
  </section>
</body>
</html>
```